Printing company needs stellar web site!

We need a website for a printing company based in Atlanta, Georgia, USA. Our company is 26 years old and just this year did a logo and branding refresh. Now we need our website to be refreshed as well.

Please see the attached source files for our new logo and stationary design.

Printing

```html
<!DOCTYPE html>
<html lang="en">
<head>
<meta charset="utf-8">
<title>PrintMeridian – Printing Services</title>
<link href="https://fonts.googleapis.com/css2?family=Open+Sans:ital,wght@0,400;0,600;0,700;1,400&display=swap" rel="stylesheet">
<style>
:root{
  --blue:#1a5ea8;
  --blue-dark:#0f3f78;
  --blue-deep:#0b2f5c;
  --blue-light:#2f7fd0;
  --page:#eef0f2;
  --panel:#ffffff;
  --cream:#f6f1e4;
  --text:#333a42;
  --muted:#6b737c;
  --line:#d5d9de;
  --orange:#f2a31b;
}
*{box-sizing:border-box;margin:0;padding:0}
html,body{width:867px;height:1200px;overflow:hidden}
body{font-family:"Open Sans",Arial,sans-serif;background:var(--page);color:var(--text);position:relative;font-size:11px}
.abs{position:absolute}

.site-header{left:0;top:0;width:867px;height:78px;background:var(--panel)}
.brand{left:30px;top:18px;display:flex;align-items:center;gap:8px}
.brand-square{width:16px;height:16px;background:var(--blue)}
.brand-name{font-weight:700;font-size:24px;color:var(--blue);line-height:1}
.brand-tag{left:30px;top:50px;font-size:9px;color:var(--muted)}
.slogan{left:450px;top:14px;width:260px;text-align:center;font-size:13px;font-style:italic;color:var(--blue-dark);line-height:1.3}
.callus{left:740px;top:12px}
.callus small{display:block;font-size:10px;color:var(--muted)}
.callus strong{font-size:16px;color:var(--blue-dark)}

.main-nav{left:30px;top:78px;width:807px;height:20px;background:linear-gradient(var(--blue-light),var(--blue-dark));display:flex}
.main-nav a{color:#fff;text-decoration:none;font-size:10px;font-weight:600;padding:0 14px;line-height:20px;border-right:1px solid rgba(255,255,255,.25)}
.main-nav a.active{background:var(--panel);color:var(--blue-dark)}

.hero{left:30px;top:98px;width:807px;height:230px;background:var(--panel)}
.badge{left:10px;top:10px;width:140px;height:96px;background:linear-gradient(#f3efe2,#e2d6b4);border-radius:6px}
.hero-photo{left:165px;top:6px;width:632px;height:190px;background:linear-gradient(135deg,#dfe6ee,#9fb8d2 50%,#4f6b8b);border-radius:3px}
.hero-caption{left:165px;top:202px;width:632px;text-align:center;font-size:11px;font-weight:700;color:var(--blue-dark)}
.arrow{top:92px;width:18px;height:18px;border-radius:50%;background:rgba(255,255,255,.9)}

.sidebar-box{left:30px;width:152px;background:var(--cream);border:1px solid var(--line);overflow:hidden}
.box-title{background:linear-gradient(var(--blue-light),var(--blue-dark));color:#fff;font-weight:700;font-size:12px;padding:4px 8px}
.cat-list{list-style:none;padding:4px 8px}
.cat-list li{font-size:9px;padding:8px 0 8px 10px;border-bottom:1px dotted var(--line);position:relative}
.cat-list li::before{content:"";position:absolute;left:0;top:12px;border-left:4px solid var(--blue);border-top:3px solid transparent;border-bottom:3px solid transparent}
.news-item{padding:5px 8px;font-size:8px;color:var(--muted);line-height:1.3;border-bottom:1px dotted var(--line)}
.more{text-align:right;font-size:9px;font-weight:700;color:var(--blue-dark);padding:4px 8px}
.newsletter p{font-size:8px;color:var(--muted);padding:5px 8px}
.signup{display:flex;margin:0 8px 8px}
.signup span{flex:1;height:16px;background:#fff;border:1px solid var(--line)}
.signup b{background:var(--blue);color:#fff;font-size:8px;padding:0 5px;line-height:16px}

.content-box{left:192px;width:645px;background:var(--panel);border:1px solid var(--line);overflow:hidden}
.content-box .box-title{display:inline-block;border-radius:0 0 6px 0}
.product-grid{display:grid;grid-template-columns:repeat(3,1fr);gap:10px 24px;padding:8px 14px 4px}
.product-img{height:100px;border-radius:2px}
.product-grid p{font-size:8px;color:var(--muted);margin-top:3px;line-height:1.3}
.services{display:flex;gap:18px;padding:8px 14px 10px}
.service{flex:1;height:72px;position:relative}
.service span{position:absolute;left:0;right:0;bottom:0;background:rgba(11,47,92,.85);color:#fff;font-size:9px;font-weight:700;text-align:center;padding:3px 0}
.clients{display:flex;justify-content:space-around;align-items:center;padding:10px 20px}
.client{font-size:14px;font-weight:600;color:var(--muted)}

.site-footer{left:0;top:975px;width:867px;height:225px;background:var(--blue-deep);color:#c9d6e6}
.foot-col h4{color:#fff;font-size:12px;margin-bottom:6px}
.foot-col p{font-size:8px;line-height:1.45}
.quote{background:var(--blue);padding:6px;font-size:8px;line-height:1.4;border-radius:3px}
.foot-brand{font-weight:700;font-size:18px;color:#fff}
.foot-nav{left:0;top:1133px;width:867px;height:26px;background:var(--blue);display:flex;align-items:center;padding-left:30px;gap:14px}
.foot-nav a{color:#fff;font-size:9px;text-decoration:none}
.foot-phone{left:590px;top:1133px;height:26px;font-size:17px;font-weight:700;color:#fff;display:flex;align-items:center;gap:6px}
.seal{left:760px;top:1118px;width:50px;height:50px;border-radius:50%;background:var(--orange)}
.copyright{left:30px;top:1174px;font-size:8px;color:#9fb3ca}
</style>
</head>
<body>
<header class="abs site-header">
  <div class="abs brand"><span class="brand-square"></span><span class="brand-name">PrintMeridian</span></div>
  <div class="abs brand-tag">Outstanding service, quality product, competitive pricing</div>
  <div class="abs slogan">We Know, we understand<br>we will exceed your expectations.</div>
  <div class="abs callus"><small>Call us</small><strong>800.555.0142</strong></div>
</header>
<nav class="abs main-nav">
  <a class="active">Home</a><a>Markets</a><a>Products</a><a>Services</a><a>About Us</a><a>Contact Us</a><a>Customer Service</a><a>FTP</a>
</nav>
<section class="abs hero">
  <div class="abs badge" role="img" aria-label="Anniversary badge"></div>
  <div class="abs hero-photo" role="img" aria-label="Hands holding a framed print with sample prints"></div>
  <div class="abs arrow" style="left:170px"></div>
  <div class="abs arrow" style="left:774px"></div>
  <div class="abs hero-caption">We Provide Outstanding Service, Quality Product &amp; Competitive Pricing.</div>
</section>

<aside class="abs sidebar-box" style="top:216px;height:404px">
  <div class="box-title">Categories</div>
  <ul class="cat-list">
    <li>4 Color Process</li><li>Color Matching</li><li>Flexible Packaging</li><li>Piggyback</li><li>Two Side Print</li><li>UV Printing</li><li>UV Varnish</li><li>Gloss and Matte Laminate</li><li>Labels</li><li>Specialty Label Constructions</li><li>Carton Substrates</li><li>Finishing Types</li>
  </ul>
</aside>
<aside class="abs sidebar-box" style="top:650px;height:190px">
  <div class="box-title">Latest News</div>
  <div class="news-item">New press line installed to speed up short label runs for local clients.</div>
  <div class="news-item">Our team now offers same week proofs on most flexible packaging jobs.</div>
  <div class="news-item">Read about our updated color matching lab and new finishing options.</div>
  <div class="more">View More »</div>
</aside>
<aside class="abs sidebar-box newsletter" style="top:880px;height:75px">
  <div class="box-title">Newsletter</div>
  <p>Get the latest updates</p>
  <div class="signup"><span></span><b>Subscribe</b></div>
</aside>

<section class="abs content-box" style="top:340px;height:368px">
  <div class="box-title">Featured Products</div>
  <div class="product-grid">
    <div><div class="product-img" role="img" aria-label="Color swatch fan" style="background:linear-gradient(135deg,#f1c36b,#d9534f,#4a7fc1)"></div><p>Short product note on label stock and finish.</p></div>
    <div><div class="product-img" role="img" aria-label="Stacked printed samples" style="background:linear-gradient(135deg,#e8e1d4,#b9a98c)"></div><p>Short product note on label stock and finish.</p></div>
    <div><div class="product-img" role="img" aria-label="Color swatch fan" style="background:linear-gradient(135deg,#7bc67b,#e8d35a,#d36a4f)"></div><p>Short product note on label stock and finish.</p></div>
    <div><div class="product-img" role="img" aria-label="Color swatch fan" style="background:linear-gradient(135deg,#e96d8a,#f3b44b,#6fb0e0)"></div><p>Short product note on label stock and finish.</p></div>
    <div><div class="product-img" role="img" aria-label="Color swatch fan" style="background:linear-gradient(135deg,#5a8fd6,#a86ccf,#e57373)"></div><p>Short product note on label stock and finish.</p></div>
    <div><div class="product-img" role="img" aria-label="Color swatch fan" style="background:linear-gradient(135deg,#f2d36b,#6cc3a0,#4a78c2)"></div><p>Short product note on label stock and finish.</p></div>
  </div>
  <div class="more">View More »</div>
</section>

<section class="abs content-box" style="top:722px;height:122px">
  <div class="box-title">Our Services</div>
  <div class="services">
    <div class="service" role="img" aria-label="Printing press at work" style="background:linear-gradient(135deg,#8fa3b8,#3e5670)"><span>PRE-PRESS</span></div>
    <div class="service" role="img" aria-label="Warehouse shelves with stock" style="background:linear-gradient(135deg,#c9a77a,#6e5a44)"><span>INVENTORY MANAGEMENT</span></div>
    <div class="service" role="img" aria-label="Consulting meeting" style="background:linear-gradient(135deg,#b8c4d0,#55667a)"><span>CONSULTING</span></div>
  </div>
</section>

<section class="abs content-box" style="top:856px;height:100px">
  <div class="box-title">Our Clients</div>
  <div class="clients">
    <span class="client">Northvale</span><span class="client">Brightline</span><span class="client">Corvex</span>
  </div>
</section>

<footer class="abs site-footer">
  <div class="abs foot-col" style="left:30px;top:14px;width:230px">
    <h4>About Us</h4>
    <p>PrintMeridian is a trusted Atlanta area printer with over two decades of experience in labels, packaging and specialty print. Our team works closely with every client to deliver on time, on budget and on color, with service that goes beyond the press.</p>
    <p style="color:#fff;font-weight:700;margin-top:6px">Read More »</p>
  </div>
  <div class="abs foot-col" style="left:300px;top:14px;width:240px">
    <h4>Testimonials</h4>
    <div class="quote">Great quality and fast turnaround on every order. The team always goes the extra mile for us and our brands.<br><b>— Client Name</b></div>
    <p style="color:#fff;font-weight:700;margin-top:6px">View All »</p>
  </div>
  <div class="abs foot-col" style="left:600px;top:14px;width:230px">
    <h4>Contact Us</h4>
    <p>1200 Harbor Works Lane<br>Marietta, GA 30060</p>
    <p style="margin-top:6px">770.555.0188</p>
    <p>hello@printmeridian.com</p>
    <div class="foot-brand" style="margin-top:10px">PrintMeridian</div>
  </div>
</footer>
<nav class="abs foot-nav">
  <a>Home</a><a>Markets</a><a>Products</a><a>Services</a><a>About Us</a><a>Contact Us</a><a>Customer Service</a><a>FTP</a>
</nav>
<div class="abs foot-phone">
  <svg width="16" height="16" viewBox="0 0 24 24"><path fill="#fff" d="M6.6 10.8a15 15 0 0 0 6.6 6.6l2.2-2.2a1 1 0 0 1 1-.25 11.4 11.4 0 0 0 3.6.57 1 1 0 0 1 1 1V20a1 1 0 0 1-1 1A17 17 0 0 1 3 4a1 1 0 0 1 1-1h3.5a1 1 0 0 1 1 1c0 1.25.2 2.45.57 3.6a1 1 0 0 1-.25 1z"/></svg>
  770.555.0188
</div>
<div class="abs seal" role="img" aria-label="Certification seal"></div>
<div class="abs copyright">© 2014 PrintMeridian. All rights reserved.</div>
</body>
</html>
```